Redesign of business card for Cedar Ridge Mechanical

We are looking for a new design for our business cards for Cedar Ridge Mechanical. We are a plumbing & HVAC construction company, operating on the West Coast of Canada and USA. Logo attached.
Industry/Entity Type
Construction - Plumbing & HVAC
Contact Information for Business Card
Name, address, phone numbers, email, website address
Look and feel
Each slider illustrates characteristics of the customer's brand and the style your logo design should communicate.

```html
<!DOCTYPE html>
<html lang="en">
<head>
<meta charset="utf-8">
<title>Cedar Ridge Mechanical – Business Card</title>
<link href="https://fonts.googleapis.com/css2?family=Open+Sans:wght@400;600;700&display=swap" rel="stylesheet">
<style>
  :root {
    --backdrop: #d8d2c8;
    --card-light: #ece6dc;
    --band-dark: #141414;
    --swoosh-taupe: #8a8275;
    --swoosh-cream: #f3eee5;
    --strip: #bdb6aa;
    --ink: #1c1c1c;
    --gold: #dccdb3;
    --muted-gold: #c9bca6;
    --web-grey: #7b766e;
  }
  * { margin: 0; padding: 0; box-sizing: border-box; }
  html, body {
    width: 1200px; height: 1047px; overflow: hidden;
    background: var(--backdrop);
    font-family: "Open Sans", Arial, sans-serif;
  }
  .card {
    position: absolute; left: 100px; top: 237px;
    width: 1000px; height: 572px;
    border-radius: 26px; overflow: hidden;
    box-shadow: 0 6px 24px rgba(0,0,0,0.18);
  }
  .card-art { position: absolute; inset: 0; }
  .brand {
    position: absolute; left: 0; right: 0; top: 108px;
    display: flex; justify-content: center; align-items: center; gap: 18px;
  }
  .brand-square { width: 34px; height: 34px; background: var(--ink); }
  .brand-name {
    font-weight: 600; font-size: 44px; color: var(--ink);
    letter-spacing: 1px; text-transform: uppercase;
  }
  .person {
    position: absolute; right: 534px; top: 348px; text-align: right;
  }
  .person-name {
    font-weight: 700; font-size: 36px; color: var(--gold); letter-spacing: 0.5px;
  }
  .person-title {
    font-size: 22px; color: var(--muted-gold); margin-top: 6px;
  }
  .divider {
    position: absolute; left: 506px; top: 340px; width: 2px; height: 124px;
    background: var(--muted-gold);
  }
  .contacts {
    position: absolute; left: 532px; top: 330px; list-style: none;
  }
  .contacts li {
    display: flex; align-items: center; gap: 6px;
    height: 34px; font-size: 25px; color: var(--gold);
  }
  .contacts svg { width: 22px; height: 22px; fill: var(--gold); flex: none; }
  .website {
    position: absolute; left: 0; right: 0; top: 510px; text-align: center;
    font-size: 23px; color: var(--web-grey);
  }
</style>
</head>
<body>
  <div class="card">
    <svg class="card-art" viewBox="0 0 1000 572" preserveAspectRatio="none" aria-hidden="true">
      <rect width="1000" height="572" fill="var(--card-light)"/>
      <path d="M0 196 Q330 330 1000 182 L1000 260 Q360 330 0 250 Z" fill="var(--swoosh-taupe)"/>
      <path d="M0 204 Q340 326 1000 196" fill="none" stroke="var(--swoosh-cream)" stroke-width="4"/>
      <path d="M0 214 Q360 340 1000 206" fill="none" stroke="var(--band-dark)" stroke-width="3"/>
      <path d="M0 240 Q380 390 1000 232 L1000 486 L0 486 Z" fill="var(--band-dark)"/>
      <rect y="486" width="1000" height="86" fill="var(--strip)"/>
    </svg>

    <div class="brand">
      <span class="brand-square"></span>
      <span class="brand-name">Cedar Ridge Mechanical</span>
    </div>

    <div class="person">
      <div class="person-name">DANIEL HAYES</div>
      <div class="person-title">Managing Director</div>
    </div>

    <div class="divider"></div>

    <ul class="contacts">
      <li>
        <svg viewBox="0 0 24 24"><path d="M6.6 10.8a15 15 0 0 0 6.6 6.6l2.2-2.2a1 1 0 0 1 1-.25 11.4 11.4 0 0 0 3.6.57 1 1 0 0 1 1 1V20a1 1 0 0 1-1 1A17 17 0 0 1 3 4a1 1 0 0 1 1-1h3.5a1 1 0 0 1 1 1c0 1.25.2 2.45.57 3.6a1 1 0 0 1-.25 1z"/></svg>
        123 456 789
      </li>
      <li>
        <svg viewBox="0 0 24 24"><path d="M6 3h12v5H6zM4 9h16a2 2 0 0 1 2 2v6h-4v4H6v-4H2v-6a2 2 0 0 1 2-2zm4 7v3h8v-3z"/></svg>
        123 456 789
      </li>
      <li>
        <svg viewBox="0 0 24 24"><path d="M8 2h8a2 2 0 0 1 2 2v16a2 2 0 0 1-2 2H8a2 2 0 0 1-2-2V4a2 2 0 0 1 2-2zm0 3v13h8V5zm4 14.2a1 1 0 1 0 0 .1z"/></svg>
        123 456 789
      </li>
      <li>
        <svg viewBox="0 0 24 24"><path d="M2 9l10-6 10 6v11H2zm2 2.2V18h16v-6.8l-8 4.8z"/></svg>
        info@cedarridgemech.com
      </li>
    </ul>

    <div class="website">www.cedarridgemech.com</div>
  </div>
</body>
</html>
```